I need a business card designed using the logo provided either vertical or horizontal......Harbourline Property Group is an Australian based real estate company that caters for the upper end of the market so the design of the business card "must reflect" the companies image!!
Colour combinations are optional but "must be realistic" and must be able to be accurately useable CMYK colours.
Please consider that any colours used "must be able to be used" and be suitable in following designs for "pull out banner signs" and "real estate signs".
The colours and the font in the attached designs are for example and other combinations are encouraged.
Target Market(s)
The High End of the Australian real estate market
Industry/Entity Type
Business
Contact Information for Business Card
Logo - Business Name - Director + Licensed Real Estate Agent - Mobile Number (Cell Phone) - Business Number - Fax - Email Address - Web address
Requirements
Must have
- Designs and colours (CMYK) that can easily be interpreted by an Australian printer.
Nice to have
- Some alternative ideas on colour and font..........the ones provided are ok and have been provided as an example but I am looking for alternative ideas
Should not have
- Loud, overly bright colours. Designs that do not reflect the professional standards of the business.
- Designs that look good on a computer monitor but can not be re-created on a printing press.............this is most important when it comes to shading etc.

```html
<!DOCTYPE html>
<html lang="en">
<head>
<meta charset="utf-8">
<title>Harbourline Property Group – Business Card</title>
<link rel="stylesheet" href="https://fonts.googleapis.com/css2?family=Open+Sans:wght@400;600&display=swap">
<style>
  :root {
    --backdrop: #3b322e;
    --card-front-dark: #1f1f20;
    --card-front-light: #5a5a5b;
    --card-back: #5b5c5e;
    --text-light: #f4f4f2;
    --text-muted: #d8d8d6;
    --accent-gold: #b9a97e;
    --brand-cream: #ece3c9;
  }
  * { box-sizing: border-box; margin: 0; padding: 0; }
  html, body { width: 1200px; height: 844px; overflow: hidden; }
  body {
    background: var(--backdrop);
    font-family: "Open Sans", Arial, sans-serif;
    position: relative;
  }
  .card {
    position: absolute;
    top: 272px;
    width: 525px;
    height: 300px;
    border-radius: 4px;
    box-shadow: 0 10px 24px rgba(0,0,0,0.45);
    overflow: hidden;
  }
  /* Front: contact side */
  .card--front {
    left: 50px;
    background: radial-gradient(ellipse at 48% 42%, var(--card-front-light) 0%, #3a3a3b 45%, var(--card-front-dark) 100%);
    color: var(--text-light);
  }
  .brand-mark {
    position: absolute;
    left: 38px;
    top: 112px;
    width: 190px;
    display: flex;
    align-items: flex-start;
    gap: 10px;
  }
  .brand-mark__square {
    flex: none;
    width: 14px;
    height: 14px;
    margin-top: 5px;
    background: var(--text-light);
  }
  .brand-mark__name {
    font-weight: 600;
    font-size: 19px;
    line-height: 1.25;
    color: var(--text-light);
  }
  .person {
    position: absolute;
    left: 250px;
    top: 58px;
  }
  .person__name {
    font-size: 17px;
    font-weight: 600;
    letter-spacing: 0.5px;
    text-transform: uppercase;
    padding-bottom: 5px;
    border-bottom: 1px solid var(--accent-gold);
    width: 185px;
  }
  .person__role {
    margin-top: 5px;
    font-size: 13px;
    color: var(--text-muted);
  }
  .contacts {
    position: absolute;
    left: 250px;
    top: 138px;
    list-style: none;
    font-size: 13px;
    line-height: 1.3;
    color: var(--text-light);
  }
  .address {
    position: absolute;
    left: 38px;
    bottom: 26px;
    font-size: 13.5px;
    color: var(--text-light);
  }
  /* Back: brand side */
  .card--back {
    left: 625px;
    background: var(--card-back);
    display: flex;
    align-items: center;
    justify-content: center;
  }
  .brand-lockup {
    display: flex;
    align-items: center;
    gap: 14px;
  }
  .brand-lockup__square {
    width: 22px;
    height: 22px;
    background: var(--brand-cream);
  }
  .brand-lockup__name {
    font-weight: 600;
    font-size: 24px;
    line-height: 1.25;
    color: var(--brand-cream);
    text-transform: uppercase;
    letter-spacing: 1px;
  }
</style>
</head>
<body>
  <section class="card card--front" aria-label="Business card, contact side">
    <div class="brand-mark">
      <span class="brand-mark__square" aria-hidden="true"></span>
      <span class="brand-mark__name">Harbourline Property Group</span>
    </div>
    <div class="person">
      <h1 class="person__name">Daniel Whitmore</h1>
      <p class="person__role">Managing Director</p>
    </div>
    <ul class="contacts">
      <li>0412-555-018</li>
      <li>02-5550-1842</li>
      <li>daniel@harbourline.com</li>
      <li>www.harbourline.com</li>
    </ul>
    <p class="address">48 Esplanade Road | Sydney, NSW | 2000</p>
  </section>

  <section class="card card--back" aria-label="Business card, brand side">
    <div class="brand-lockup">
      <span class="brand-lockup__square" aria-hidden="true"></span>
      <span class="brand-lockup__name">Harbourline<br>Property Group</span>
    </div>
  </section>
</body>
</html>
```